Award-winnning Estate Agent needs a premium version of their 'For Sale' board design

We need a premium option for our 'For Sale' board design. We have a standard board that is attached to this brief, but were are looking to have a premium design version that we will use when selling exclusive properties. Our company name is Harbourline Vale Estates and the name for this is exclusive selection is: 'The Harbourline Collection'. The design needs to work with our current brand, but have a distinctive PREMIUM feel to it. I have uploaded the barnd guidelines and also some of the exisisting logo variations. We do NOT need a new logo but feel free to play around with colours, fonts, sizes etc. for the sign.

Target Market(s)

Property buyers & house hunters

Industry/Entity Type

Real Estate - Residential Property

Font styles to use
Sans Serif

Requirements
Must have
• A premium fee, must be square design, must be easy to read when driving past the sign
Nice to have
• I'm open ot ideas

```html
<!DOCTYPE html>
<html lang="en">
<head>
<meta charset="utf-8">
<title>Harbourline Vale Estates – For Sale Board</title>
<link rel="stylesheet" href="https://fonts.googleapis.com/css2?family=Tinos:wght@700&display=swap">
<style>
  :root {
    --board-gold: #c4a465;
    --ink-black: #000000;
    --paper-white: #ffffff;
  }
  * { box-sizing: border-box; margin: 0; padding: 0; }
  html, body {
    width: 1200px;
    height: 1199px;
    overflow: hidden;
    background: var(--board-gold);
  }
  .board {
    position: relative;
    width: 1200px;
    height: 1199px;
    background: var(--board-gold);
    font-family: "Tinos", "Times New Roman", serif;
    font-weight: 700;
    color: var(--ink-black);
    white-space: nowrap;
  }
  .brand-chevron {
    position: absolute;
    left: 0;
    top: 0;
    width: 1200px;
    height: 400px;
  }
  .brand-name {
    position: absolute;
    left: 0;
    top: 266px;
    width: 1200px;
    text-align: center;
    color: var(--paper-white);
    font-size: 34px;
    line-height: 42px;
    letter-spacing: 7px;
    text-transform: uppercase;
  }
  .collection-title {
    position: absolute;
    left: 0;
    top: 434px;
    width: 1200px;
    text-align: center;
    font-size: 58px;
    line-height: 70px;
    text-transform: uppercase;
    letter-spacing: 0.5px;
  }
  .sale-band {
    position: absolute;
    left: 0;
    top: 513px;
    width: 1200px;
    height: 246px;
    background: var(--ink-black);
    color: var(--paper-white);
    display: flex;
    align-items: center;
    justify-content: center;
    font-size: 206px;
    line-height: 1;
    letter-spacing: 2px;
    padding-top: 10px;
  }
  .phone-box {
    position: absolute;
    left: 112px;
    top: 790px;
    width: 986px;
    height: 270px;
    background: var(--ink-black);
    border-radius: 56px;
    color: var(--paper-white);
    display: flex;
    align-items: center;
    justify-content: center;
    font-size: 156px;
    line-height: 1;
    padding-top: 8px;
  }
  .web-address {
    position: absolute;
    left: 0;
    top: 1080px;
    width: 1200px;
    text-align: center;
    font-size: 76px;
    line-height: 84px;
    text-transform: lowercase;
  }
</style>
</head>
<body>
  <main class="board">
    <svg class="brand-chevron" viewBox="0 0 1200 400" aria-hidden="true">
      <polygon points="112,0 1098,0 1098,214 614,397 112,214" fill="var(--ink-black)"/>
    </svg>
    <div class="brand-name">Harbourline Vale<br>Estates</div>
    <h2 class="collection-title">The Harbourline Collection</h2>
    <h1 class="sale-band">FOR SALE</h1>
    <div class="phone-box">01632 960418</div>
    <div class="web-address">harbourlinevaleestates.co.uk</div>
  </main>
</body>
</html>
```